Banner Ad Design Project

We need a 728x90 and a 300x250
1st option
"I have a lead for you. Click here to close the deal."
In large bold letters.
Under this in smaller letters,
"Lornavel. For serious business networkers"
2nd option
"Put that coffee down!"
"Coffee's for closers only."
Close more deals. LORNAVEL LOGO
(this is a quote from Harrowmere Tide. It is a famous sales movie)
The other option is
"First you get the money" "Then you get the power" in bold letters.
"Lornavel. For serious business networkers" in smaller letters at the bottom.
-Must have our colors
-Must have our logo (Small at the bottom right)
-Watch the video at lornavel () com
Please be creative. If the banner can have multiple images that would be great as well.
This needs to be a serious looking ad that is bold and clean.
Updates
Please be sure to use the phrase, "Put that coffee down! Coffee's for closers only" with the logo and at the bottom the words, Lornavel, for serious business networkers. in one of the designs. This will be our first campaign. I am looking for a very simple design that is bold. Perhaps just a coffee cup with the words and no other graphics.
Target Market(s)
Sales professionals
Industry/Entity Type
Business
Look and feel

```html
<!DOCTYPE html>
<html lang="en">
<head>
<meta charset="utf-8">
<title>Lornavel banner set</title>
<link rel="stylesheet" href="https://fonts.googleapis.com/css2?family=Arimo:wght@400;700&display=swap">
<style>
  :root {
    --stage: #333333;
    --band-blue: #30619a;
    --band-orange: #f2a11b;
    --band-green: #5e9535;
    --paper: #ffffff;
    --ink-light: #ffffff;
    --brand-blue: #2c5a94;
    --brand-orange: #f2a11b;
    --brand-green: #5e9535;
    --muted: #c4c4c4;
    --photo-dark: #2a2a2e;
    --photo-light: #e9e6e2;
    --streak-blue: #b9cbe0;
    --streak-orange: #f7dcae;
    --streak-green: #cfe0c0;
  }
  * { margin: 0; padding: 0; box-sizing: border-box; }
  html, body { width: 667px; height: 1200px; overflow: hidden; background: var(--stage); }
  body { position: relative; font-family: "Arimo", Arial, sans-serif; }

  .banner {
    position: absolute;
    left: 135px;
    width: 400px;
    height: 333px;
    background: var(--paper);
    overflow: hidden;
  }
  .banner--lead { top: 73px; }
  .banner--close { top: 435px; }
  .banner--close-soft { top: 796px; }

  .headline { list-style: none; }
  .headline__band {
    height: 54px;
    display: flex;
    align-items: center;
    justify-content: center;
    color: var(--ink-light);
    font-weight: 700;
    font-size: 38px;
    letter-spacing: 2px;
    line-height: 1;
  }
  .headline__band--blue { background: var(--band-blue); }
  .headline__band--orange { background: var(--band-orange); }
  .headline__band--green { background: var(--band-green); }

  .scene { position: relative; height: 171px; box-shadow: inset 0 6px 6px -4px rgba(0,0,0,0.15); }

  .scene__photo {
    position: absolute;
    left: 10px;
    top: 22px;
    width: 150px;
    height: 149px;
    background: linear-gradient(160deg, var(--photo-light) 0%, #b8b2ab 35%, var(--photo-dark) 75%);
    border-radius: 40px 40px 0 0;
  }

  .scene__streaks { position: absolute; left: 150px; top: 50px; }

  .brand {
    position: absolute;
    left: 248px;
    top: 34px;
    width: 120px;
    display: flex;
    flex-direction: column;
    align-items: center;
    gap: 8px;
  }
  .brand__mark { width: 62px; height: 62px; background: var(--brand-blue); }
  .brand__name { font-size: 17px; font-weight: 700; color: var(--brand-blue); letter-spacing: 0.5px; }
  .banner--close-soft .brand { opacity: 0.5; }

  .cta-join {
    position: absolute;
    left: 248px;
    width: 120px;
    top: 146px;
    text-align: center;
    font-size: 17px;
    font-weight: 700;
    color: var(--muted);
    letter-spacing: 0.5px;
  }
  .banner--close .brand, .banner--close-soft .brand { top: 26px; }
</style>
</head>
<body>

  <section class="banner banner--lead">
    <ul class="headline">
      <li class="headline__band headline__band--blue">I have</li>
      <li class="headline__band headline__band--orange">a lead</li>
      <li class="headline__band headline__band--green">for you</li>
    </ul>
    <div class="scene">
      <svg class="scene__streaks" width="120" height="40" viewBox="0 0 120 40" aria-hidden="true">
        <polygon points="0,14 120,0 120,10 0,24" fill="var(--streak-blue)"/>
        <polygon points="0,24 120,10 120,20 0,32" fill="var(--streak-orange)"/>
        <polygon points="0,32 120,20 120,30 0,40" fill="var(--streak-green)"/>
      </svg>
      <div class="scene__photo" role="img" aria-label="Businessman in a dark suit and red tie reading a tablet"></div>
      <div class="brand">
        <span class="brand__mark"></span>
        <span class="brand__name">lornavel</span>
      </div>
    </div>
  </section>

  <section class="banner banner--close">
    <ul class="headline">
      <li class="headline__band headline__band--blue">Click here</li>
      <li class="headline__band headline__band--orange">to close</li>
      <li class="headline__band headline__band--green">the deal</li>
    </ul>
    <div class="scene">
      <svg class="scene__streaks" width="120" height="40" viewBox="0 0 120 40" aria-hidden="true">
        <polygon points="0,14 120,0 120,10 0,24" fill="var(--streak-blue)"/>
        <polygon points="0,24 120,10 120,20 0,32" fill="var(--streak-orange)"/>
        <polygon points="0,32 120,20 120,30 0,40" fill="var(--streak-green)"/>
      </svg>
      <div class="scene__photo" role="img" aria-label="Businessman in a dark suit and red tie reading a tablet"></div>
      <div class="brand">
        <span class="brand__mark"></span>
        <span class="brand__name">lornavel</span>
      </div>
      <p class="cta-join">Join Us!</p>
    </div>
  </section>

  <section class="banner banner--close-soft">
    <ul class="headline">
      <li class="headline__band headline__band--blue">Click here</li>
      <li class="headline__band headline__band--orange">to close</li>
      <li class="headline__band headline__band--green">the deal</li>
    </ul>
    <div class="scene">
      <svg class="scene__streaks" width="120" height="40" viewBox="0 0 120 40" aria-hidden="true">
        <polygon points="0,14 120,0 120,10 0,24" fill="var(--streak-blue)"/>
        <polygon points="0,24 120,10 120,20 0,32" fill="var(--streak-orange)"/>
        <polygon points="0,32 120,20 120,30 0,40" fill="var(--streak-green)"/>
      </svg>
      <div class="scene__photo" role="img" aria-label="Businessman in a dark suit and red tie reading a tablet"></div>
      <div class="brand">
        <span class="brand__mark"></span>
        <span class="brand__name">lornavel</span>
      </div>
      <p class="cta-join">Join Us!</p>
    </div>
  </section>

</body>
</html>
```